Real Estate Company Looking for Business Card Designs for 3 Executives

Hello!
Thanks so much for considering our project! We are a real estate investment company located in Edmonton, Alberta called Bellhaven Group of Companies. We invest/develop both commercial and residential real estate and are looking to create 3 DOUBLE-SIDED business cards for 3 top executives in the company! (for some reason it won't let us select the double-sided option, but yes, the cards are double sided and would be happy to tip extra)

We have certain guidelines that we want our business cards to for sure follow - the back of the Business card has to be the Black Background Version of the Logo which has already been designed and linked as a file (first file). We want the entire back of the card to simply just be the black background logo. In terms of the front of the card, would like to see a smaller version of the white background logo (linked as the second file) in the top left hand corner - of course, feel free to get creative and we can make revisions together along the way! and Then after that, just text. We want the card to be sharp, clean, easy on the eyes and highly professional looking. We would like the card to include the Full name of the Company (Bellhaven Group of Companies), Name of the Person, Title, Phone, Email. If possible please provide the front part of the card for 3 people:

1) Bellhaven Group of Companies, Liora Quenby, Chief Financial Officer, 780-555-0142, lioraquenby@bellhavengroup.example

2) Bellhaven Group of Companies, Tobias Quenby, Chief Executive Officer, 780-555-0187, tobiasquenby@bellhavengroup.example

3) Bellhaven Group of Companies, Rui Delcourt, Chief Operations Officer, 587-555-0163, ruidelcourt@bellhavengroup.example

Thank you so much for considering our project & we look forward to seeing your designs!

```html
<!DOCTYPE html>
<html lang="en">
<head>
<meta charset="utf-8">
<title>Bellhaven Group of Companies – Liora Quenby</title>
<link rel="stylesheet" href="https://fonts.googleapis.com/css2?family=Barlow+Condensed:wght@300;400;600;700&display=swap">
<style>
  :root {
    --ink: #0b0b0b;
    --paper: #ffffff;
  }
  * { margin: 0; padding: 0; box-sizing: border-box; }
  html, body {
    width: 686px;
    height: 1200px;
    overflow: hidden;
    background: var(--paper);
  }
  .card {
    position: relative;
    width: 686px;
    height: 1200px;
    background: var(--paper);
    font-family: "Barlow Condensed", "Arial Narrow", sans-serif;
    color: var(--ink);
  }
  .brand-square {
    position: absolute;
    left: 253px;
    top: 197px;
    width: 180px;
    height: 180px;
    background: var(--ink);
  }
  .brand-name {
    position: absolute;
    left: 0;
    width: 686px;
    top: 452px;
    text-align: center;
    font-size: 40px;
    font-weight: 400;
    letter-spacing: 1.1em;
    padding-left: 1.1em;
    line-height: 1;
  }
  .person-name {
    position: absolute;
    left: 0;
    width: 686px;
    top: 596px;
    text-align: center;
    font-size: 56px;
    font-weight: 700;
    line-height: 1;
  }
  .name-rule {
    position: absolute;
    left: 195px;
    width: 295px;
    top: 665px;
    height: 2px;
    background: var(--ink);
  }
  .person-title {
    position: absolute;
    left: 0;
    width: 686px;
    top: 680px;
    text-align: center;
    font-size: 35px;
    font-weight: 300;
    line-height: 1.1;
  }
  .stripe {
    position: absolute;
    left: 0;
    width: 686px;
    background: var(--ink);
  }
  .stripe-thin { top: 816px; height: 4px; }
  .stripe-mid { top: 829px; height: 9px; }
  .contact-panel {
    position: absolute;
    left: 0;
    top: 847px;
    width: 686px;
    height: 353px;
    background: var(--ink);
    color: var(--paper);
  }
  .contact-line {
    position: absolute;
    left: 0;
    width: 686px;
    display: flex;
    justify-content: center;
    align-items: center;
    gap: 12px;
    font-size: 36px;
    font-weight: 300;
    line-height: 1;
  }
  .contact-line svg { fill: var(--paper); flex: none; }
  .contact-phone { top: 62px; }
  .contact-email { top: 120px; }
  .company-name {
    position: absolute;
    left: 0;
    width: 686px;
    top: 201px;
    text-align: center;
    font-size: 39px;
    font-weight: 700;
    letter-spacing: 0.13em;
    padding-left: 0.13em;
    line-height: 51px;
    text-transform: uppercase;
  }
</style>
</head>
<body>
  <main class="card">
    <div class="brand-square"></div>
    <div class="brand-name">BELLHAVEN</div>

    <h1 class="person-name">Liora Quenby</h1>
    <div class="name-rule"></div>
    <p class="person-title">Chief Financial Officer</p>

    <div class="stripe stripe-thin"></div>
    <div class="stripe stripe-mid"></div>

    <section class="contact-panel">
      <p class="contact-line contact-phone">
        <svg width="32" height="36" viewBox="0 0 24 24" aria-hidden="true">
          <path d="M6.6 10.8a15.1 15.1 0 0 0 6.6 6.6l2.2-2.2c.3-.3.7-.4 1-.2 1.1.4 2.3.6 3.6.6.6 0 1 .4 1 1V20c0 .6-.4 1-1 1A17 17 0 0 1 3 4c0-.6.4-1 1-1h3.5c.6 0 1 .4 1 1 0 1.3.2 2.5.6 3.6.1.3 0 .7-.2 1l-2.3 2.2z"/>
        </svg>
        <span>780-555-0142</span>
      </p>
      <p class="contact-line contact-email">
        <svg width="40" height="28" viewBox="0 0 40 28" aria-hidden="true">
          <path d="M0 0h40v28H0z M3 3v1l17 12L37 4V3z M3 7v18h34V7L20 19z" fill-rule="evenodd"/>
        </svg>
        <span>lioraquenby@bellhavengroup.example</span>
      </p>
      <p class="company-name">Bellhaven Group<br>of Companies</p>
    </section>
  </main>
</body>
</html>
```